business card - Helicopter Flight Services, Flight School, etc.

We need a business card design for a new helicopter service.

We offer Helicopter Flight Services, Aerial Filming & Photography, Flight School, and Helicopter Tours. In that order.

Summit BladeAir, Inc.
Dennis Tollerby
SummitBladeair@Kestmail.com
626-418-7352

Based at the Brenwick Airport in Van Nuys, CA. The final design should communicate integrity and safety. Pictures or logos at your discretion.

Card back side - surprise me.

```html
<!DOCTYPE html>
<html lang="en">
<head>
<meta charset="utf-8">
<title>Summit BladeAir, Inc. — Business Card</title>
<link rel="stylesheet" href="https://fonts.googleapis.com/css2?family=Open+Sans:wght@400;700&display=swap">
<style>
  :root {
    --page: #e9e7e3;
    --card-white: #ffffff;
    --card-dark: #2b2b2c;
    --brand-blue: #3f82c7;
    --charcoal: #404142;
    --ink: #1f1f1f;
    --soft-white: #f2f2f2;
  }
  * { box-sizing: border-box; margin: 0; padding: 0; }
  html, body {
    width: 1200px; height: 900px; overflow: hidden;
    background: var(--page);
    font-family: "Open Sans", Arial, sans-serif;
  }
  .sheet {
    width: 1200px; height: 900px;
    display: flex; flex-direction: column; align-items: center; justify-content: center;
    gap: 56px;
  }
  .card {
    position: relative;
    width: 620px; height: 354px;
    overflow: hidden;
    box-shadow: 0 6px 18px rgba(0,0,0,.18);
  }

  /* Back side */
  .card--back { background: var(--card-dark); color: var(--soft-white); }
  .card--back .brand {
    position: absolute; left: 0; right: 0; top: 92px;
    display: flex; align-items: center; justify-content: center; gap: 16px;
  }
  .brand-dot {
    width: 26px; height: 26px; border-radius: 50%;
    background: currentColor;
  }
  .brand-name {
    font-weight: 700; font-size: 38px; letter-spacing: 3px;
    text-transform: uppercase; line-height: 1;
  }
  .services {
    position: absolute; left: 0; right: 0; top: 196px;
    text-align: center; font-size: 17px; line-height: 1.7; font-weight: 400;
  }

  /* Front side */
  .card--front { background: var(--card-white); color: var(--ink); }
  .corner-mark { position: absolute; left: 0; top: 0; }
  .holder-name {
    position: absolute; left: 68px; top: 20px;
    color: var(--brand-blue); font-weight: 700; font-size: 20px;
  }
  .card--front .brand {
    position: absolute; left: 300px; top: 128px;
    display: flex; align-items: center; gap: 12px;
    color: var(--brand-blue);
  }
  .card--front .brand-name { font-size: 30px; letter-spacing: 2px; }
  .card--front .brand-dot { width: 22px; height: 22px; }
  .contact {
    position: absolute; left: 40px; top: 214px;
    list-style: none; font-size: 17px; line-height: 1.55;
  }
  .contact li { display: flex; align-items: center; gap: 10px; }
  .contact svg { flex: none; }
  .edge-bands { position: absolute; left: 0; bottom: 0; }
</style>
</head>
<body>
<main class="sheet">

  <section class="card card--back" aria-label="Card back">
    <div class="brand">
      <span class="brand-dot"></span>
      <span class="brand-name">Summit BladeAir Inc.</span>
    </div>
    <p class="services">
      Helicopter Flight Services | Aerial Filming &amp; Photography<br>
      Flight School | Helicopter Tours
    </p>
  </section>

  <section class="card card--front" aria-label="Card front">
    <svg class="corner-mark" width="64" height="60" viewBox="0 0 64 60" aria-hidden="true">
      <rect x="0" y="0" width="64" height="18" fill="var(--charcoal)"/>
      <polygon points="40,0 58,0 58,56 8,56" fill="var(--brand-blue)"/>
    </svg>
    <h1 class="holder-name">Dennis Tollerby</h1>

    <div class="brand">
      <span class="brand-dot"></span>
      <span class="brand-name">Summit BladeAir Inc.</span>
    </div>

    <ul class="contact">
      <li>
        <svg width="14" height="14" viewBox="0 0 24 24" aria-hidden="true"><path fill="var(--brand-blue)" d="M6.6 10.8a15.1 15.1 0 006.6 6.6l2.2-2.2c.3-.3.7-.4 1-.2 1.1.4 2.3.6 3.6.6.6 0 1 .4 1 1V20c0 .6-.4 1-1 1A17 17 0 013 4c0-.6.4-1 1-1h3.5c.6 0 1 .4 1 1 0 1.3.2 2.5.6 3.6.1.3 0 .7-.2 1z"/></svg>
        626-418-7352
      </li>
      <li>
        <svg width="14" height="12" viewBox="0 0 24 18" aria-hidden="true"><rect width="24" height="18" rx="2" fill="var(--brand-blue)"/><path d="M2 2l10 8 10-8" stroke="#fff" stroke-width="2" fill="none"/></svg>
        SummitBladeair@Kestmail.com
      </li>
    </ul>

    <svg class="edge-bands" width="620" height="100" viewBox="0 0 620 100" aria-hidden="true">
      <polygon points="0,18 22,18 0,60" fill="var(--charcoal)"/>
      <polygon points="0,60 22,18 250,18 230,60" fill="var(--charcoal)"/>
      <polygon points="0,60 230,60 210,100 0,100" fill="var(--card-white)"/>
      <polygon points="260,60 620,60 620,100 240,100" fill="var(--brand-blue)"/>
    </svg>
  </section>

</main>
</body>
</html>
```